White Paper and One-Page Advertisement for TELVORISH-QM

I need both documents to be better formatted and designed so they look professional, not something someone with mediocre word skills put together. They will go out to 1000s of industry professionals, and they need to look sharp. I need them to have my company's color palate logo, and branding on it similar to how it is now, but better. Please do not change any of the written content, but it can be arranged in any other format you think is better. Smart art and things i've already used can be omitted in favor of better designs. The developer is free to use their creativity. White paper should not be longer than the three pages unless necessary.

Target Market(s)

Life Sciences supply chain professionals

Colors
33b8a4
0592cd
9bcb3c
fbee3e
3277b5

Requirements
Must have
• Must be professional looking and not look like something done in word. Please use the color palate as seen on the documents.
Should not have
• Any changes to the written content.

```html
<!DOCTYPE html>
<html lang="en">
<head>
<meta charset="utf-8">
<title>TELVORISH-QM White Paper – Changing Pharma's Paradigm of Waste</title>
<link href="https://fonts.googleapis.com/css2?family=Rajdhani:wght@700&family=Titillium+Web:wght@600;700&family=Open+Sans:wght@400;600;700&display=swap" rel="stylesheet">
<style>
:root{
  --ink:#3a3a3a;
  --deep:#0a3f3a;
  --forest:#0f5e4c;
  --green:#1b8a5a;
  --lime:#9bcb3c;
  --teal:#33b8a4;
  --sky:#0592cd;
  --blue:#3277b5;
  --paper:#ffffff;
  --stage-light:#d8d9da;
  --stage-dark:#3b3b3c;
}
*{margin:0;padding:0;box-sizing:border-box}
html,body{width:899px;height:1200px;overflow:hidden}
body{background:linear-gradient(var(--stage-light) 0 932px,var(--stage-dark) 932px);font-family:"Open Sans",sans-serif;color:var(--ink);position:relative}
.page{position:absolute;width:379px;height:536px;background:var(--paper);overflow:hidden;box-shadow:0 2px 6px rgba(0,0,0,.25)}
.p-info{left:67px;top:60px}
.p-cover{left:453px;top:60px;background:linear-gradient(160deg,var(--forest),var(--green) 60%,var(--deep))}
.p-overview{left:67px;top:602px}
.p-solutions{left:453px;top:602px}
.band{position:absolute;left:0;top:0;width:100%;height:62px}
.band-title{position:absolute;font-family:"Titillium Web",sans-serif;font-weight:700;color:#fff;font-size:14px}
.footer{position:absolute;left:0;bottom:0;width:100%;height:14px;background:linear-gradient(90deg,var(--deep),var(--forest))}
.footer::before{content:"";position:absolute;left:0;top:-3px;width:100%;height:3px;background:var(--lime)}
.col{position:absolute;font-size:4.5px;line-height:1.35}
.col p{margin-bottom:3px}
.col h4{font-family:"Titillium Web",sans-serif;font-size:6px;color:var(--ink);margin:4px 0 2px}
.col ul{padding-left:8px;margin-bottom:3px}
.col li{margin-bottom:1px}
.photo{position:absolute;border-radius:1px}
.brand{position:absolute;display:flex;align-items:center;gap:5px;font-family:"Titillium Web",sans-serif;font-weight:700}
.brand .dot{border-radius:50%;border:2px solid var(--lime)}
.lime-h{font-family:"Titillium Web",sans-serif;font-weight:700;font-size:12px;color:#fff}
.stats{display:flex;gap:2px;margin:3px 0}
.stat{flex:1;background:#eef6e4;font-size:4px;text-align:left}
.stat b{display:block;background:var(--lime);color:#fff;text-align:center;font-size:5.5px;padding:1px 0;margin-bottom:1px}
.stat span{display:block;padding:0 2px 2px}
.pill{background:var(--deep);color:#fff;border-radius:8px;padding:3px 6px;font-size:4.3px;font-weight:700;text-align:center;margin:3px 0}
.tags{display:grid;grid-template-columns:1fr 1fr;gap:4px;margin:5px 0}
.tag{color:#fff;font-size:5px;font-weight:600;text-align:center;padding:4px 0;border-radius:3px;border:1px solid rgba(0,0,0,.2)}
.barrier{color:#fff;font-size:5px;font-weight:700;padding:2px 5px;border-radius:0 8px 8px 0;width:150px;margin:4px 0 2px}
.vision{position:absolute;width:118px;height:118px;border-radius:50%;background:radial-gradient(var(--forest),var(--deep));border:3px solid var(--teal);color:#fff;text-align:center;font-size:5.3px;line-height:1.3;padding:18px 12px 0}
.vision b{display:block;font-size:7px;margin-bottom:4px}
.vision p{margin-bottom:4px}
</style>
</head>
<body>

<!-- Back page: How to Find Out More -->
<section class="page p-info">
  <svg class="band" viewBox="0 0 379 62" preserveAspectRatio="none">
    <defs><linearGradient id="hdrA" x1="0" x2="1"><stop offset="0" stop-color="#0a3f3a"/><stop offset="1" stop-color="#137a5e"/></linearGradient></defs>
    <path d="M0 0H379V30C300 38 240 46 180 58H0Z" fill="url(#hdrA)"/>
    <path d="M180 58C240 46 300 38 379 30V36C300 44 250 52 210 58Z" fill="#9bcb3c"/>
  </svg>
  <h2 class="band-title" style="left:12px;top:26px">How to Find Out More</h2>

  <div class="col" style="left:14px;top:70px;width:160px">
    <p>The exciting new marketplace called TELVORISH-QM is scheduled for initial launch 03 November 2018.</p>
    <h4 style="font-size:6.5px;font-weight:600">For more information:</h4>
    <ul style="font-size:5.6px;padding-left:22px;list-style:disc">
      <li>Email Dana Whitlock</li>
      <li>Visit www.telvorishqm.com</li>
      <li>Call 844-555-TLQM</li>
    </ul>
    <p>*WE enable a greener, more cost-efficient, and quality driven supply chain through a collaborative life sciences marketplace.</p>
    <p>*WE are an emerging small business with the ultimate goal to educate, inspire, and align Pharma around a new paradigm of waste optimization and sourcing strategies.</p>
    <p>*WE aspire to increase medicine access around the world and decrease Pharma's overall environmental impact</p>
    <h4 style="font-size:6.5px;font-weight:600;margin-top:10px">Sources</h4>
    <h4>1. Top 100 Pharma Companies</h4>
    <p style="padding-left:8px">•https://pharmaledger-review.example.org/media/market/top100-league-tables.pdf</p>
    <h4>2. 2016 Annual/10K Reports</h4>
    <p style="padding-left:8px">•Twenty leading global pharma manufacturers, annual filings and financial statements for fiscal year 2016.</p>
    <h4>3. Total Pharma Revenue 2016</h4>
    <p style="padding-left:8px">•http://chemjournal-archive.example.org/doi/pdfplus/10.2016/rev</p>
    <h4>4. Currency Exchange Rates 29 Jan 2018</h4>
    <p style="padding-left:8px">•http://www.fxrates-demo.example.com/table/?from=USD</p>
    <h4>5. Pricing Pressure</h4>
    <p style="padding-left:8px">•http://medreview-journal.example.org/full/pricing</p>
  </div>

  <p class="col" style="left:188px;top:76px;width:175px;text-align:center;color:var(--green);font-size:5px;font-weight:600">Every new journey of change and innovation we take is for them...<br>The Patient</p>
  <div class="photo" role="img" aria-label="Photo of a baby in a knitted hat" style="left:190px;top:90px;width:173px;height:125px;background:linear-gradient(135deg,#c9b6a4,#8f7a68)"></div>
  <div class="photo" role="img" aria-label="Photo of a smiling elderly woman with glasses" style="left:190px;top:222px;width:173px;height:125px;background:linear-gradient(135deg,#b9c2a8,#6e745f)"></div>
  <div class="photo" role="img" aria-label="Photo of a young woman outdoors" style="left:190px;top:359px;width:173px;height:125px;background:linear-gradient(135deg,#8a8e7a,#3f4334)"></div>

  <div class="brand" style="left:22px;top:455px;font-size:13px;color:var(--green)">
    <span class="dot" style="width:20px;height:20px"></span>TELVORISH-QM
  </div>
  <div class="footer"></div>
</section>

<!-- Cover -->
<section class="page p-cover">
  <h1 style="position:absolute;right:26px;top:56px;text-align:right;font-family:'Rajdhani',sans-serif;font-weight:700;font-size:28px;line-height:1.15;color:var(--lime);letter-spacing:.3px">CHANGING PHARMA'S<br>PARADIGM OF WASTE</h1>
  <p style="position:absolute;right:26px;top:138px;text-align:right;font-family:'Titillium Web',sans-serif;font-weight:600;font-size:11.5px;line-height:1.3;color:#fff">How Pharma's Demand Volatility Could<br>Be Costing You Millions in Material<br>Write-downs &amp; Procurement</p>
  <p style="position:absolute;right:26px;top:210px;text-align:right;font-family:'Titillium Web',sans-serif;font-weight:600;font-size:11.5px;line-height:1.3;color:#fff">Dana Whitlock<br>August 2018</p>

  <svg style="position:absolute;left:0;top:0" width="379" height="536" viewBox="0 0 379 536">
    <path d="M0 255C110 280 260 250 379 170V536H0Z" fill="#fff"/>
    <path d="M0 250C110 272 260 240 379 160V175C260 255 110 285 0 262Z" fill="#9bcb3c"/>
    <path d="M0 470C120 500 260 480 379 420V536H0Z" fill="#0f5e4c"/>
    <path d="M0 462C120 492 260 472 379 410V420C260 482 120 502 0 472Z" fill="#9bcb3c"/>
  </svg>
  <div class="photo" role="img" aria-label="Photo of a nurse in blue scrubs caring for a smiling elderly patient" style="left:110px;top:290px;width:269px;height:200px;border-radius:0;clip-path:polygon(18% 0,100% 0,100% 100%,0 100%,0 40%);background:linear-gradient(120deg,#e9ecec,#8dc6cf 55%,#5a9fa9)"></div>
  <div class="brand" style="left:24px;top:270px;font-size:9px;color:var(--green)">
    <span class="dot" style="width:30px;height:30px"></span>TELVORISH-QM
  </div>
</section>

<!-- Inside left: Overview & Baseline Problem -->
<section class="page p-overview">
  <svg class="band" viewBox="0 0 379 62" preserveAspectRatio="none">
    <defs><linearGradient id="hdrC" x1="0" x2="1"><stop offset="0" stop-color="#0a3f3a"/><stop offset="1" stop-color="#137a5e"/></linearGradient></defs>
    <path d="M0 0H379V24C300 30 250 40 180 58H0Z" fill="url(#hdrC)"/>
    <path d="M180 58C250 40 300 30 379 24V58H180Z" fill="#9bcb3c"/>
  </svg>
  <h2 class="band-title" style="left:12px;top:28px">Overview</h2>
  <h2 class="lime-h" style="position:absolute;left:238px;top:40px">Baseline Problem</h2>

  <div class="col" style="left:12px;top:66px;width:160px">
    <p>Demand volatility is a challenge for every supply chain. It strikes at the end of supply chains causing a "bullwhip effect" that becomes exponentially more impactful further back in the chain. For Pharma, the effect is strongest in manufacturing and procurement, specifically with starting raw materials and consumables. Swings in demand can cripple launches, cause stock-outs, inflate material prices, make lean planning ineffective, and cause significant write-downs of residual/obsolete materials; ultimately inflating CoGS and reducing net income. These swings can also cause inventory costs to inflate, materials to expire or become obsolete, higher disposal fees, and a larger carbon footprint. The yearly financial impacts are staggering considering Pharma's economic footprint. Twenty of Pharma's top 100 companies were sampled using 2015 &amp; 2016 financial figures. Industry estimates for waste include:</p>
    <div class="stats">
      <div class="stat"><b>3.77%</b><span>Avg Raw Material Write-down as a % of net income</span></div>
      <div class="stat"><b>$2.7B</b><span>Est Pharma Written Down Inventory in 2016</span></div>
      <div class="stat"><b>$2,034</b><span>Est US Pharma Revenue per 1 Ton Non-MSW Waste</span></div>
      <div class="stat"><b>.01</b><span>Correlation Coefficient of Material Write-downs and firm size</span></div>
    </div>
    <p>What Do These Numbers Mean?</p>
    <ul><li>3.77% is an alarmingly high, and does not include capitalized consumables, equipment disposal, and similar wastes</li></ul>
    <div class="pill">+$5B in net income LS Firm: est $185M in write-downs<br>+$50M in net income LS Firm: est $1.9M in write-downs</div>
    <ul>
      <li>$2.7B is likely much lower than the real figure due to capitalizing consumable inventories for launches etc.</li>
      <li>.01 correlation coefficient means this problem does not discriminate based on company size and is ubiquitous in the industry.</li>
      <li>$2,034 to one ton of industrial waste is not progressive.</li>
    </ul>
    <p>Industries have attempted to mitigate the bullwhip effect through many techniques and systems such as ERP, robust forecasting models, demand management, LSS tools, strategic sourcing, etc. However, life science firms still struggle to effectively address this problem as evidenced by the write-down figures. Many non-FDA regulated industries have started utilizing marketplaces and brokerage services to create circular supply chains that optimize waste by connecting buyers and sellers. However, Pharma and life sciences have yet to adopt this waste-centric supply chain and execute it in a manner conducive to the compliance and indemnification requirements of the industry.</p>
    <p><b>A life sciences marketplace and consortium</b> for manufacturers, researchers, and vendors can minimize the aforementioned problems by quickly, innovatively, and transparently exchanging material information in safe and controlled environments.</p>
    <p>It is a call to arms among supply chain, procurement, and quality leaders to take part in a more circular, greener, and collaborative supply chain. Time is critical as global competition grows.</p>
    <p>Let's explore <b>Current</b> and <b>Future State</b> of this industry issue to understand why such a marketplace can begin the much-needed transition for life science companies.</p>
  </div>

  <div class="col" style="left:186px;top:66px;width:180px">
    <h4>What?</h4>
    <ul><li>Disposal of high quality materials, equipment, spare parts</li><li>Single and/or limited sources of supply</li><li>Inability to collaborate with like-minded life sciences firms</li><li>High CoGS due to materials write-downs</li><li>High inventory carrying costs</li><li>Greater business continuity risk</li><li>High disposal costs</li><li>Larger environmental footprint</li><li>Stock-out of materials</li></ul>
    <h4>Who?</h4>
    <ul><li>FDA Regulated Industries, Procurement, Quality, Production, and Finance.</li></ul>
    <h4>Where &amp; When</h4>
    <ul><li>Commercial &amp; clinical production, R&amp;D, sourcing/purchasing, production planning, quality testing, etc.</li><li>Volatile demand periods, e.g., product intro growth, decline, seasonality, economic uncertainty, and unforeseen events.</li></ul>
    <h4>How do we know it's there?</h4>
    <ul><li>We physically see it taking place, and it's in our data.</li></ul>
    <h4>Triple Bottom Line Impact</h4>
    <p><i>Financial</i> — Vendors/Sellers: higher write-downs and 3rd party disposal fees. Buyers: lost sales and stock-outs, inflated market value of materials and supplier expedition fees, higher costs due to bullwhip effect.</p>
    <p><i>Environment</i> — Greater contribution to global warming through landfill addition, incineration, inactivation, and energy consumption. Noncompliance with environmental standards.</p>
    <p><i>Society</i> — Lost community trust, high environment and consumer costs, less innovation, collaboration, and supply chain optimization.</p>
    <h4>Current State</h4>
    <p><i>External Solutions</i> — Pharma and other FDA industries spend considerable energy on reducing waste. A plethora of techniques are employed to mitigate, prepare for, respond to, and recover from the bullwhip effect, which is one of the leading causes of write-downs and waste. However, such efforts are predicated on:</p>
    <div class="tags">
      <div class="tag" style="background:var(--lime)">Forecast Accuracy</div>
      <div class="tag" style="background:var(--lime)">Supplier Reliability</div>
      <div class="tag" style="background:var(--green)">Process Variability</div>
      <div class="tag" style="background:var(--teal)">External Environment</div>
    </div>
    <p>While not fruitless, attempts to mitigate the above external influences are extremely unpredictable and have never solved pharma's write-down, inefficiency, stock-out, and environmental problems.</p>
    <h4>Internal Solutions</h4>
    <p>The next effort involves reducing obsolescence by making use of materials within the firm. Typically, interplant demand is the only outlet to optimize surplus earmarked for a reserve/write-down. Even this involves many of the same regulatory compliance, quality, and economic challenges, takes time, resources, and does not provide a broad network to utilize.</p>
    <h4>Environmental Solutions</h4>
    <p>FDA industries, like most others, make attempts to reuse, recycle, and convert to energy where applicable. However, they're unable to conduct these activities for perishable, expiring, and/or consumable materials.</p>
  </div>
  <div class="footer"></div>
</section>

<!-- Inside right: Undesirable Solutions & Root Cause -->
<section class="page p-solutions">
  <svg class="band" viewBox="0 0 379 62" preserveAspectRatio="none">
    <defs><linearGradient id="hdrD" x1="0" x2="1"><stop offset="0" stop-color="#137a5e"/><stop offset="1" stop-color="#0a3f3a"/></linearGradient></defs>
    <path d="M0 0H379V58H190C140 40 80 30 0 26Z" fill="url(#hdrD)"/>
    <path d="M0 26C80 30 140 40 190 58H0Z" fill="#9bcb3c"/>
  </svg>
  <h2 class="lime-h" style="position:absolute;left:12px;top:40px">Undesirable Solutions</h2>

  <div class="col" style="left:12px;top:66px;width:155px">
    <p>Unfortunately, third party disposal (frequently landfill) is typically the first and most popular option as perishable, expiring, and complex materials are generally unable to be reused or recycled. These disposals come in many forms to include responsible landfills, incineration, inactivation, etc.</p>
    <h4>Overall</h4>
    <p>Industries spend much capital and resources to reduce write-downs in an environment where the bullwhip effect reigns supreme. Mitigations to this effect are attempted but only partially successful or sustainable.</p>
    <h4>Refined Problem</h4>
    <p>There is no clear market leader that helps organizations optimize waste, collaborate to reduce it, and market more quality materials to more firms whether for research, manufacturing, or donations. This marketplace must be regulated and all participants properly vetted and authenticated. Accounts must be created to enable companies to post materials and request information. The marketplace must facilitate collaborative relationships between companies that help them reduce supply chain costs. It must quickly, economically, compliantly, and legally facilitate these exchanges.</p>
    <h4>Contemporary Operating Environment</h4>
    <ul><li>Constant pressure from global competition, increasing customer and governmental demand on price, more regulatory scrutiny, and a relentless societal pursuit of sustainability are eroding the once high margins for Pharma.</li><li>Regulators are cooperative and open to solutions.</li><li>Exchanges and consortiums are not typically leveraged in Pharma.</li><li>Pharma continues to struggle with the bullwhip effect.</li></ul>
    <h4>Barriers</h4>
    <div class="barrier" style="background:var(--lime)">Compliance</div>
    <p>It is the responsibility of manufacturers to provide customers safe and efficacious products. There is a misperception that high quality materials cannot be sourced from aftermarket exchanges.</p>
    <div class="barrier" style="background:var(--lime)">Liability</div>
    <p>Contractual agreements with suppliers have clauses for poor quality. There is a misperception these cannot be implemented at the marketplace level.</p>
    <div class="barrier" style="background:var(--teal)">Economics</div>
    <p>Exchanges can be difficult due to time/effort. A sanctioned marketplace can provide the structure to make it easy.</p>
    <div class="barrier" style="background:var(--sky)">Sustainability</div>
    <p>Firms have not discovered how to leverage exchanges to reduce environmental footprint and enable certifications and trust.</p>
    <div class="barrier" style="background:var(--teal)">Confidence</div>
    <p>Trust is critical to firms. They should know a marketplace has properly vetted members with KPI data for analysis.</p>
    <div class="barrier" style="background:var(--lime)">Confidence</div>
    <p>Exchanges should be fast. An innovative marketplace can ensure quick exchanges.</p>
  </div>

  <h2 style="position:absolute;left:193px;top:68px;font-family:'Titillium Web',sans-serif;font-weight:700;font-size:12.5px;color:var(--green)">Root Cause &amp; Paradigm Shift</h2>
  <div class="col" style="left:193px;top:88px;width:174px">
    <p>Comfort in the status quo has enabled a culture of waste. With life science margins so high, it hasn't been a priority to solve. Additionally, there hasn't been an effective means to deal with waste. This limits the industry's ability to leverage these marketplaces. Finally, misperceived issues of liability and quality have strained innovation; all solvable problems.</p>
    <h4>Future State</h4>
    <p>Creation of Private Virtual Life Sciences Multi-Vendor Marketplace &amp; Consortium where researchers, manufacturers, and original-end manufacturers can create a simple storefront for their organization and transact materials, equipment, parts, and collaborative relationships in a compliant and professional environment. This marketplace uses software logic that leverages auditing capabilities of buyers and sellers by making required data and documentation visible and subject to data integrity standards, thus enabling transactions in a fast and compliant manner.</p>
    <h4>Benefits</h4>
    <ul><li>Avoid write-downs for surplus material/consumable stock</li><li>Continue production when stocked-out of materials</li><li>Reduce purchase price of materials</li><li>Risk pool safety stock to reduce amount required</li><li>Allow for leaner planning in that stock-outs can be addressed</li><li>Allow for more responsive planning with an outlet to sell SS</li><li>Reduce supplier audit resources and costs</li><li>Reduce environment footprint by avoiding disposal fees</li></ul>
  </div>

  <div class="vision" style="left:213px;top:265px">
    <b>VISION</b>
    <p>1. A collaborative and compliant multi vendor marketplace is part of Pharma's normal operating practices</p>
    <p>2. Waste is not tolerated in the life sciences industry</p>
    <p>3. There is always a compliant outlet</p>
  </div>
  <span style="position:absolute;left:309px;top:356px;width:18px;height:18px;border-radius:50%;background:var(--lime)"></span>

  <div class="col" style="left:193px;top:395px;width:174px">
    <h4>How to Implement</h4>
    <p>Application of the following guidance, regulations, and bodies will drive exchange process and design:</p>
    <ul><li>ICH Q7 (International harmonized cGMP standards)</li><li>CFR Title 21 (US cGMP standards)</li><li>Data Integrity Draft Guidance (good doc practices)</li><li>GMP for Pharmaceutical Products (global health standards)</li><li>Good Manufacturing Practices in Active Pharmaceutical Ingredients Development, 1999</li><li>Supplier Qualification and Management Guidelines</li></ul>
    <h4><i>Data Integrity</i></h4>
    <p>Data integrity will drive how the exchange operates. All parties are encouraged to use ALCOA-Plus review documents associated with transactions. This enables buyers' standards of data integrity and cGMP quality compliance to be adhered.</p>
  </div>
  <div class="footer"></div>
</section>

</body>
</html>
```